PHGCCUL re-branding website and logo

We are looking for a new webpage design and logo our current page address is www.phgccul-example.org. We want to create a new design using PHGCCUL Pinewood and Harbour Growers Co-operative Credit Union limited and another with the purposed new name PHFC Pinewood and Harbour Financial Co-operative, the color scheme is purple and burnt orange. Our new logo and webpage should communicate change and growth purposed theme continuing our legacy here to server past, present and future generations. Our idea for the logo is a live shot of hands of different ages in a circle holding a tree

Target Market(s)

Everyone

Contact Information for Business Card

Company Name
Telephone number
Address
slot to enter employee info

Logo Text

(P & H) Pinewood And Harbour Financial Co-operative

Coding

Coded - Design and coding required

Number of Pages Required

2 page

Colors
f37122
fbed22
6b449b

Requirements
Must have
• links for social media

```html
<!DOCTYPE html>
<html lang="en">
<head>
<meta charset="utf-8">
<title>PHFC – Pinewood and Harbour Financial Co-operative</title>
<link href="https://fonts.googleapis.com/css2?family=Open+Sans:wght@400;600;700&display=swap" rel="stylesheet">
<style>
:root{
  --orange:#f37122;
  --ink:#1a1a1a;
  --text:#666;
  --muted:#888;
  --band:#f5f5f5;
  --footer:#f7f7f7;
  --rule:#d6d6d6;
  --icon:#8a8a8a;
  --white:#fff;
}
*{box-sizing:border-box;margin:0;padding:0}
html,body{width:725px;height:1200px;overflow:hidden}
body{font-family:"Open Sans",Arial,sans-serif;color:var(--text);background:var(--white);position:relative}
.abs{position:absolute}
.btn{position:absolute;background:var(--orange);color:var(--white);border-radius:2px;display:flex;align-items:center;justify-content:center;font-size:6.4px;box-shadow:0 1px 2px rgba(0,0,0,.2)}

/* header */
.site-header{position:absolute;left:0;top:0;width:725px;height:70px;background:var(--white)}
.brand{position:absolute;display:flex;align-items:center;gap:8px}
.brand-circle{flex:none;border-radius:50%;background:var(--orange)}
.brand-text{font-weight:600;color:var(--ink)}
.brand-name{font-size:15px;line-height:1;letter-spacing:.5px}
.brand-tag{font-size:4.6px;line-height:1.4;margin-top:3px;width:80px}
.top-phone{left:474px;top:19px;font-size:6.4px;color:var(--muted);display:flex;align-items:center;gap:5px}
.teller{left:566px;top:16px;width:80px;height:18px;font-size:6.4px}
.main-nav{position:absolute;top:50px;right:79px;display:flex;font-size:6.8px;color:var(--muted)}
.main-nav span{margin-left:24px}
.main-nav .active{color:var(--orange)}

/* hero */
.hero{position:absolute;left:0;top:70px;width:725px;height:284px;background:linear-gradient(100deg,#b9c6dc 0%,#9fb0cc 35%,#c7a89a 60%,#8a9bbb 100%)}
.hero-title{left:79px;top:70px;font-size:24px;color:var(--orange);font-weight:400}
.hero-text{left:79px;top:113px;width:242px;font-size:8.4px;color:var(--white);line-height:14px;text-align:justify}
.hero-btn{left:79px;top:156px;width:99px;height:30px;font-size:9.6px}
.dots{left:80px;top:200px;display:flex;gap:3px}
.dots i{width:7px;height:7px;border-radius:50%;background:#ddd;border:1px solid #ccc}
.dots i.on{background:var(--orange);border-color:var(--orange)}

.section-title{position:absolute;left:0;width:725px;text-align:center;color:var(--orange);font-weight:400}

/* welcome */
.welcome-text{left:79px;top:416px;width:567px;font-size:5.9px;line-height:11.6px;text-align:center}

/* services */
.services{position:absolute;left:0;top:532px;width:725px;height:264px;background:var(--band)}
.service{position:absolute;top:88px;width:160px;text-align:center}
.service svg{display:block;margin:0 auto}
.service h3{font-weight:400;color:var(--orange);font-size:12.4px;margin-top:10px}
.service p{font-size:6.1px;line-height:11.5px;margin-top:7px}
.service .btn{position:relative;margin:11px auto 0;width:50px;height:19px}

/* news */
.news-item{position:absolute;top:888px;width:270px}
.news-photo{position:absolute;left:0;top:0;width:111px;height:91px}
.news-body{position:absolute;left:127px;top:0;width:143px}
.news-date{font-size:6.1px;color:var(--ink);margin-top:-2px}
.news-body h3{font-weight:400;color:var(--orange);font-size:12px;margin-top:2px}
.news-body p{font-size:6.1px;line-height:11.5px;margin-top:3px}
.news-body .btn{position:relative;width:50px;height:19px;margin-top:6px}

/* footer */
.site-footer{position:absolute;left:0;top:1014px;width:725px;height:186px;background:var(--footer)}
.social{left:80px;top:96px;display:flex;gap:3.5px}
.social span{width:19px;height:19px;border:1px solid #333;border-radius:50%}
.footer-col h4{font-weight:400;color:var(--orange);font-size:8.4px}
.footer-col ul{list-style:none;font-size:6px;margin-top:9px}
.footer-col li{height:14.5px}
.newsletter p{font-size:6px;line-height:14.5px;width:150px;margin-top:6px}
.mail-input{position:absolute;left:0;top:59px;width:152px;height:24px;border:1px solid #ddd;background:var(--white);font-size:6px;padding:8px 9px;color:var(--text)}
.subscribe{left:2px;top:96px;width:50px;height:17px}
.contact li{display:flex;align-items:center;gap:8px;height:16.5px}
.contact svg{flex:none}
.footer-rule{left:79px;top:151px;width:567px;height:1px;background:var(--rule)}
.copyright{left:0;top:165px;width:725px;text-align:center;font-size:6.1px}
</style>
</head>
<body>

<header class="site-header">
  <div class="brand" style="left:79px;top:13px">
    <div class="brand-circle" style="width:40px;height:40px"></div>
    <div class="brand-text">
      <div class="brand-name">PHFC</div>
      <div class="brand-tag">Pinewood and Harbour Financial Co-operative</div>
    </div>
  </div>
  <div class="abs top-phone">
    <svg width="7" height="7" viewBox="0 0 10 10"><path d="M2 0.5l2 2.2-1 1.3c.7 1.4 1.6 2.3 3 3l1.3-1 2.2 2-1 1.8C4.5 9.5.5 5.5.3 1.6z" fill="#f37122"/></svg>
    Phone: (555) 410-2730
  </div>
  <div class="btn teller">Internet Teller Login</div>
  <nav class="main-nav">
    <span class="active">Home</span><span>Apply For A Loan</span><span>Become A Member</span><span>My Credit Union</span><span>Products and Services</span><span>Tools and Benefits</span>
  </nav>
</header>

<section class="hero" role="img" aria-label="Photo of hands typing on a laptop while holding a bank card">
  <h1 class="abs hero-title">Financial Co-operative</h1>
  <p class="abs hero-text">We are rebranding with the name as PHFC Pinewood and Harbour Financial Co-operative.</p>
  <div class="btn hero-btn">Learn More</div>
  <div class="abs dots"><i class="on"></i><i></i><i></i></div>
</section>

<section class="welcome">
  <h2 class="section-title" style="top:379px;font-size:21.5px">Welcome to PHFC</h2>
  <p class="abs welcome-text">Nemo enim ipsam voluptatem quia voluptas sit aspernatur aut odit aut fugit, sed quia consequuntur magni dolores eos qui ratione voluptatem sequi nesciunt. Neque porro quisquam est, qui dolorem ipsum quia dolor sit amet, consectetur, adipisci velit, sed quia non numquam eius modi tempora incidunt ut labore et dolore magnam aliquam quaerat voluptatem.Ut enim ad minima veniam, quis nostrum exercitationem ullam corporis suscipit laboriosam, nisi ut aliquid ex ea commodi consequatur? Quis autem vel eum iure reprehenderit qui in ea voluptate velit esse quam nihil molestiae consequatur, vel illum qui dolorem eum fugiat quo voluptas nulla pariatur</p>
  <div class="btn" style="left:338px;top:478px;width:50px;height:19px">Read More</div>
</section>

<section class="services">
  <h2 class="section-title" style="top:31px;font-size:21px">Our Services</h2>
  <div class="service" style="left:78px">
    <svg width="24" height="24" viewBox="0 0 24 24"><path d="M11 2.5A10 10 0 1 0 21.5 13H11z" fill="#8a8a8a"/><path d="M13 0.5V11h10.5A10.5 10.5 0 0 0 13 .5z" fill="#8a8a8a"/></svg>
    <h3>Consumer Loans</h3>
    <p>Lorem ipsum dolor sit amet, consectetur adipiscing elit, sed do eiusmod tempor incididunt ut labore et dolore magna aliqua.</p>
    <div class="btn">Read More</div>
  </div>
  <div class="service" style="left:283px">
    <svg width="28" height="24" viewBox="0 0 28 24"><path d="M6 4h16l3 8v8h-4v3h-3v-3H10v3H7v-3H3v-8z" fill="#8a8a8a"/><path d="M8 6h12l2 6H6z" fill="#f5f5f5"/><circle cx="7.5" cy="16" r="2" fill="#f5f5f5"/><circle cx="20.5" cy="16" r="2" fill="#f5f5f5"/></svg>
    <h3>Auto/Motorcycle</h3>
    <p>Lorem ipsum dolor sit amet, consectetur adipiscing elit, sed do eiusmod tempor incididunt ut labore et dolore magna aliqua.</p>
    <div class="btn">Read More</div>
  </div>
  <div class="service" style="left:490px">
    <svg width="24" height="24" viewBox="0 0 24 24"><path d="M12 3L1 12h3v9h6v-6h4v6h6v-9h3z" fill="#8a8a8a"/><rect x="16" y="4" width="3" height="5" fill="#8a8a8a"/></svg>
    <h3>Mortgages</h3>
    <p>Lorem ipsum dolor sit amet, consectetur adipiscing elit, sed do eiusmod tempor incididunt ut labore et dolore magna aliqua.</p>
    <div class="btn">Read More</div>
  </div>
</section>

<section class="news">
  <h2 class="section-title" style="top:826px;font-size:20.5px">News &amp; Events</h2>
  <article class="news-item" style="left:79px">
    <div class="news-photo" role="img" aria-label="Photo of a customer paying with a card at a café table" style="background:linear-gradient(135deg,#6d4a34,#a9835f 55%,#4b6a8a)"></div>
    <div class="news-body">
      <div class="news-date">Mar 10,2017</div>
      <h3>Consumer Loans</h3>
      <p>Lorem ipsum dolor sit amet, consectetur adipiscing elit, sed do eiusmod tempor incididunt ut labore et dolore magna aliqua.</p>
      <div class="btn">Read More</div>
    </div>
  </article>
  <article class="news-item" style="left:374px">
    <div class="news-photo" role="img" aria-label="Photo of a hand holding a card over a laptop keyboard" style="background:linear-gradient(135deg,#e6e6e6,#b8b8b8 50%,#6a6a6a)"></div>
    <div class="news-body">
      <div class="news-date">Mar 10,2017</div>
      <h3>Consumer Loans</h3>
      <p>Lorem ipsum dolor sit amet, consectetur adipiscing elit, sed do eiusmod tempor incididunt ut labore et dolore magna aliqua.</p>
      <div class="btn">Read More</div>
    </div>
  </article>
</section>

<footer class="site-footer">
  <div class="brand" style="left:80px;top:32px">
    <div class="brand-circle" style="width:48px;height:48px"></div>
    <div class="brand-text">
      <div class="brand-name" style="font-size:20px">PHFC</div>
      <div class="brand-tag" style="font-size:5.4px;width:110px">Pinewood and Harbour Financial Co-operative</div>
    </div>
  </div>
  <div class="abs social">
    <span role="link" aria-label="Social media link"></span><span role="link" aria-label="Social media link"></span><span role="link" aria-label="Social media link"></span><span role="link" aria-label="Social media link"></span>
  </div>

  <div class="abs footer-col" style="left:262px;top:23px">
    <h4>Sitemap</h4>
    <ul><li>Home</li><li>Apply For A Loan</li><li>Become A Member</li><li>Locations</li></ul>
  </div>

  <div class="abs footer-col newsletter" style="left:360px;top:23px;width:160px;height:120px">
    <h4>Newsletter</h4>
    <p>Enter your email address to receive the latest news and notes from our blog.</p>
    <div class="mail-input">Enter Your Mail Id</div>
    <div class="btn subscribe">SUBSCRIBE</div>
  </div>

  <div class="abs footer-col contact" style="left:537px;top:23px">
    <h4>Contact us</h4>
    <ul>
      <li><svg width="7" height="7" viewBox="0 0 10 10"><path d="M1 3h8v6H1z M3 1h4v3H3z" fill="#555"/></svg>(555) 410-2730</li>
      <li><svg width="7" height="7" viewBox="0 0 10 10"><rect x="2.5" y="0.5" width="5" height="3" fill="#555"/><rect x="0.5" y="3.5" width="9" height="4" fill="#555"/><rect x="2.5" y="6.5" width="5" height="3" fill="#555"/></svg>(555) 410-2741</li>
      <li><svg width="7" height="6" viewBox="0 0 10 8"><rect x="0.5" y="0.5" width="9" height="7" fill="none" stroke="#555"/><path d="M.5 .5l4.5 4 4.5-4" fill="none" stroke="#555"/></svg><span style="text-decoration:underline">info@phgccul-example.org</span></li>
      <li><svg width="6" height="8" viewBox="0 0 8 10"><path d="M4 0a3.5 3.5 0 0 1 3.5 3.5C7.5 6 4 10 4 10S.5 6 .5 3.5A3.5 3.5 0 0 1 4 0z" fill="#555"/><circle cx="4" cy="3.5" r="1.3" fill="#f7f7f7"/></svg>Harbour Road &amp; Pinewood Ave.</li>
    </ul>
  </div>

  <div class="abs footer-rule"></div>
  <p class="abs copyright">©2017 phgccul-example.org, All Rights Reserved.</p>
</footer>

</body>
</html>
```